Polish brewery needs BEER LABEL design for WEDDINGS

We need beer label design for weddings. Our brewery is located on South of Poland and it is called Warsztat Kominek [PL]/Workshop Hearth [ENG]. We feel strong connection to mountains and we use water from the mountain in our vicinity.
Regarding beer style it is India Pale Ale so beer is bitter and aromatic because of high addition of hops. Label design has to be modern and simple. We would prefer bright and cream colors.
We need to have opportunity to edit data which are on the label so we will need to get appropriate files.
In attached files you can find all details. If any additional information will be required please do not hesitate and contact with me.

Target Market(s)

Weddings

Font styles to use
Sans Serif
Script

Colors
ffffff

Requirements
Must have
• Information listed in documents in attached files
Nice to have
• Some nice graphics
Bright and cream colors.
Should not have
• -

```html
<!DOCTYPE html>
<html lang="pl">
<head>
<meta charset="utf-8">
<title>Etykieta weselna IPA – Warsztat Kominek</title>
<link rel="stylesheet" href="https://fonts.googleapis.com/css2?family=Arimo:wght@400;700&family=Yellowtail&family=Kaushan+Script&display=swap">
<style>
  :root {
    --paper: #ffffff;
    --ink: #111111;
    --frame: #1f4d60;
    --frame-light: #6f97a8;
    --hop-blue: #1b7fc4;
    --hop-light: #a9d3ee;
    --wreath-gold: #e3b27a;
    --wreath-green: #b9cdb5;
  }
  * { box-sizing: border-box; margin: 0; padding: 0; }
  html, body { width: 1200px; height: 533px; overflow: hidden; background: var(--paper); }
  .label {
    position: relative; width: 1200px; height: 533px;
    background: var(--paper); color: var(--ink);
    font-family: "Arimo", Arial, sans-serif;
  }
  .label__frame {
    position: absolute; left: 8px; top: 8px; width: 1185px; height: 518px;
    border: 3px solid var(--frame);
  }
  .label__frame-inner {
    position: absolute; left: 13px; top: 13px; width: 1175px; height: 508px;
    border: 1px solid var(--frame-light);
  }
  .corner-ornament {
    position: absolute; width: 46px; height: 46px;
    background: radial-gradient(circle at 30% 30%, var(--frame-light), var(--frame) 70%);
    opacity: .85;
  }
  .corner-ornament--tl { left: 10px; top: 10px; border-radius: 0 0 46px 0; }
  .corner-ornament--tr { right: 10px; top: 10px; border-radius: 0 0 0 46px; }
  .corner-ornament--bl { left: 10px; bottom: 10px; border-radius: 0 46px 0 0; }
  .corner-ornament--br { right: 10px; bottom: 10px; border-radius: 46px 0 0 0; }

  .panel { position: absolute; border: 2px dashed var(--ink); }
  .panel--info { left: 44px; top: 47px; width: 332px; height: 440px; }
  .panel--story { left: 820px; top: 47px; width: 331px; height: 440px; }

  .rule { position: absolute; background: var(--ink); }
  .rule--thick { height: 3px; }
  .rule--thin { height: 1px; }

  .text { position: absolute; white-space: nowrap; }
  .heading { font-weight: 700; font-size: 20px; }
  .body { font-size: 17.5px; line-height: 23px; }

  .ingredients { left: 54px; top: 58px; }
  .ingredients .body { white-space: normal; width: 310px; }
  .storage { left: 54px; top: 233px; font-size: 17.5px; line-height: 28px; white-space: normal; width: 312px; }
  .volume { left: 54px; top: 312px; }
  .address { left: 54px; top: 371px; font-size: 17.5px; line-height: 22.6px; }

  .brand-mark { position: absolute; left: 286px; top: 420px; width: 80px; text-align: center; }
  .brand-mark__square { display: block; width: 26px; height: 26px; margin: 0 auto 6px; background: var(--ink); }
  .brand-mark__name { font-size: 15px; font-weight: 700; line-height: 16px; color: var(--ink); }

  .wreath {
    position: absolute; left: 500px; top: 24px; width: 208px; height: 200px;
    background: radial-gradient(circle, var(--paper) 52%, var(--wreath-gold) 60%, var(--wreath-green) 72%, var(--paper) 78%);
  }
  .couple {
    position: absolute; left: 500px; width: 208px; text-align: center;
    font-family: "Yellowtail", cursive; font-size: 34px; color: var(--ink);
  }
  .couple--first { top: 72px; }
  .couple--second { top: 132px; }
  .couple__heart { position: absolute; left: 590px; top: 116px; }

  .divider-flourish {
    position: absolute; left: 553px; width: 94px; height: 40px;
    background: linear-gradient(90deg, transparent, #555 50%, transparent);
    opacity: .35; border-radius: 20px;
  }
  .divider-flourish--top { top: 232px; }
  .divider-flourish--bottom { top: 470px; }

  .wedding-date {
    position: absolute; left: 500px; top: 278px; width: 200px; text-align: center;
    font-family: "Kaushan Script", cursive; font-size: 32px; color: var(--ink);
  }

  .story {
    position: absolute; left: 828px; top: 55px; width: 316px;
    font-size: 17.5px; line-height: 22.6px; text-align: justify; white-space: normal;
  }
  .stats { position: absolute; left: 834px; top: 234px; }
  .stats__row { position: absolute; left: 0; height: 30px; display: flex; align-items: center; font-size: 19px; width: 200px; }
  .stats__label { width: 90px; }
  .stats__value { color: var(--hop-blue); font-size: 19px; display: flex; gap: 5px; align-items: center; }
  .links { position: absolute; left: 834px; top: 410px; font-size: 17.5px; line-height: 22.6px; }
  .links b { font-weight: 700; }
</style>
</head>
<body>
<div class="label">
  <div class="label__frame"></div>
  <div class="label__frame-inner"></div>
  <div class="corner-ornament corner-ornament--tl" role="img" aria-label="Ozdobny narożnik ramki"></div>
  <div class="corner-ornament corner-ornament--tr" role="img" aria-label="Ozdobny narożnik ramki"></div>
  <div class="corner-ornament corner-ornament--bl" role="img" aria-label="Ozdobny narożnik ramki"></div>
  <div class="corner-ornament corner-ornament--br" role="img" aria-label="Ozdobny narożnik ramki"></div>

  <!-- Info panel -->
  <div class="panel panel--info"></div>
  <div class="text ingredients">
    <div class="heading">Składniki:</div>
    <div class="body">woda, słód jęczmienny, chmiel, liście limonki, drożdże.</div>
  </div>
  <div class="rule rule--thick" style="left:54px;top:134px;width:309px"></div>
  <div class="rule rule--thin" style="left:54px;top:231px;width:310px"></div>
  <div class="text storage">Przechowywać w suchym i chłodnym miejscu</div>
  <div class="rule rule--thin" style="left:54px;top:310px;width:310px"></div>
  <div class="text volume">
    <div class="heading">Objętość butelki:</div>
    <div class="body">330ml</div>
  </div>
  <div class="rule rule--thick" style="left:54px;top:363px;width:309px"></div>
  <div class="text address">
    Warsztat Kominek<br>
    34-520 Sosnowa Polana<br>
    Browar Pod Jodłą<br>
    Leśna 12, Dębowiec<br>
    34-610
  </div>
  <div class="brand-mark">
    <span class="brand-mark__square"></span>
    <div class="brand-mark__name">WARSZTAT<br>KOMINEK</div>
  </div>

  <!-- Centre -->
  <div class="wreath" role="img" aria-label="Wieniec z zielonych liści i złotej geometrycznej ramki"></div>
  <div class="couple couple--first">Amelia</div>
  <svg class="couple__heart" width="28" height="24" viewBox="0 0 28 24" aria-hidden="true">
    <path d="M14 23 C4 15 0 11 0 6 C0 2 3 0 7 0 C10 0 12 2 14 5 C16 2 18 0 21 0 C25 0 28 2 28 6 C28 11 24 15 14 23Z" fill="var(--ink)"/>
  </svg>
  <div class="couple couple--second">Julian</div>

  <div class="divider-flourish divider-flourish--top" role="img" aria-label="Ozdobny zawijas"></div>
  <svg style="position:absolute;left:426px;top:267px" width="350" height="12" viewBox="0 0 350 12" aria-hidden="true">
    <line x1="10" y1="6" x2="340" y2="6" stroke="var(--ink)" stroke-width="2.5"/>
    <ellipse cx="7" cy="6" rx="6" ry="3.5" fill="none" stroke="var(--ink)" stroke-width="2"/>
    <ellipse cx="343" cy="6" rx="6" ry="3.5" fill="none" stroke="var(--ink)" stroke-width="2"/>
  </svg>
  <div class="wedding-date">15.3.20</div>
  <svg style="position:absolute;left:530px;top:320px" width="142" height="10" viewBox="0 0 142 10" aria-hidden="true">
    <line x1="0" y1="5" x2="55" y2="5" stroke="var(--ink)" stroke-width="1.5"/>
    <line x1="87" y1="5" x2="142" y2="5" stroke="var(--ink)" stroke-width="1.5"/>
    <circle cx="71" cy="5" r="2.5" fill="var(--ink)"/>
  </svg>
  <svg style="position:absolute;left:530px;top:388px" width="142" height="10" viewBox="0 0 142 10" aria-hidden="true">
    <line x1="0" y1="5" x2="55" y2="5" stroke="var(--ink)" stroke-width="1.5"/>
    <line x1="87" y1="5" x2="142" y2="5" stroke="var(--ink)" stroke-width="1.5"/>
    <circle cx="71" cy="5" r="2.5" fill="var(--ink)"/>
  </svg>
  <svg style="position:absolute;left:426px;top:460px" width="350" height="12" viewBox="0 0 350 12" aria-hidden="true">
    <line x1="10" y1="6" x2="340" y2="6" stroke="var(--ink)" stroke-width="2.5"/>
    <ellipse cx="7" cy="6" rx="6" ry="3.5" fill="none" stroke="var(--ink)" stroke-width="2"/>
    <ellipse cx="343" cy="6" rx="6" ry="3.5" fill="none" stroke="var(--ink)" stroke-width="2"/>
  </svg>
  <div class="divider-flourish divider-flourish--bottom" role="img" aria-label="Ozdobny zawijas"></div>

  <!-- Story panel -->
  <div class="panel panel--story"></div>
  <p class="story">Trzymasz w ręku naszą autorską IPA do produkcji której wykorzystujemy wodę wypływającą z samego serca Beskidu Wysokiego - Babiej Góry. <span style="display:block;text-align:left">IPA lubi chmiele i goryczkę, ale żeby nie było nudno postanowiliśmy ją wzbogacić limonką.</span></p>
  <div class="rule rule--thick" style="left:830px;top:223px;width:310px"></div>
  <div class="stats">
    <div class="stats__row" style="top:0"><span class="stats__label">ALK</span><span class="stats__value" style="margin-left:2px">5,5%</span></div>
    <div class="stats__row" style="top:33px"><span class="stats__label">IBU</span>
      <span class="stats__value">
        <svg width="86" height="30" viewBox="0 0 86 30" aria-hidden="true">
          <ellipse cx="12" cy="15" rx="10" ry="13" fill="var(--hop-blue)"/>
          <ellipse cx="38" cy="15" rx="10" ry="13" fill="var(--hop-blue)"/>
          <ellipse cx="64" cy="15" rx="10" ry="13" fill="var(--hop-light)"/>
        </svg>
      </span></div>
    <div class="stats__row" style="top:68px"><span class="stats__label">EBC</span>
      <span class="stats__value">
        <svg width="70" height="30" viewBox="0 0 70 30" aria-hidden="true">
          <rect x="7" y="2" width="8" height="26" rx="4" fill="var(--hop-blue)"/>
          <rect x="27" y="2" width="8" height="26" rx="4" fill="var(--hop-light)"/>
          <rect x="47" y="2" width="8" height="26" rx="4" fill="var(--hop-light)"/>
        </svg>
      </span></div>
    <div class="stats__row" style="top:101px"><span class="stats__label">EXT</span><span class="stats__value" style="margin-left:4px">14%</span></div>
    <div class="stats__row" style="top:134px"><span class="stats__label">WATER</span>
      <span class="stats__value">
        <svg width="30" height="34" viewBox="0 0 30 34" aria-hidden="true">
          <path d="M15 1 C10 10 2 16 2 22 A13 11 0 0 0 28 22 C28 16 20 10 15 1Z" fill="var(--hop-blue)"/>
        </svg>
      </span></div>
  </div>
  <div class="rule rule--thick" style="left:830px;top:401px;width:310px"></div>
  <div class="links">
    <div><b>FB</b> - warsztatkominek</div>
    <div><b>INSTA</b> - warsztat.kominek</div>
    <div><b>WEBSITE</b> - www.warsztatkominek.pl</div>
  </div>
</div>
</body>
</html>
```